Business card for Eyelash extension salon in Beverly Hills,California USA

We need new business card for our salon in Beverly Hills. The salon name is 'Lashvera' . We would like to have...Business name: Lashvera Name of person: will provide later Address 4720 N.Alder Crest Ave Beverly Hills , CA 90210 Phone: will provide later (Text only) Web: www.lashverastudio.example Snapgrid icon, Circlebook icon follow us for seasonal campaign and news @lashverastudiolounge Design should look elegant, high-end, clean, simple, cohesive with my brand. Please refer my brand board. Business name color will be metallic bronzy color. Im thinking grey background or white background. Thanks

Target Market(s)

25-35. Gender neutral. People who are in Entertainment business industry.
This is High-end Eyelash extension salon in Beverly Hills

Industry/Entity Type

Beauty Salon

Contact Information for Business Card

Business name: Lashvera
Name of person: will provide later
Address 4720 N.Alder Crest Ave Beverly Hills , CA 90210
Phone: will provide later (Text only)
Web: www.lashverastudio.example
Snapgrid icon, Circlebook icon
follow us for seasonal campaign and news @lashverastudiolounge

Requirements
Must have
• Beautiful, elegant, clean and simple look but very attractive and modern
Should not have
• We don't like too clutter, too busy designs.

```html
<!DOCTYPE html>
<html lang="en">
<head>
<meta charset="UTF-8">
<title>Lashvera – Business Card</title>
<link href="https://fonts.googleapis.com/css2?family=Bodoni+Moda:wght@400;600&display=swap" rel="stylesheet">
<style>
  :root {
    --backdrop: #3b3b3d;
    --card: #ffffff;
    --bronze: #87634a;
    --ink: #3a2f29;
    --photo-light: #f2f2f2;
    --photo-mid: #d6d6d6;
    --photo-shade: #b9b9b9;
  }
  * { margin: 0; padding: 0; box-sizing: border-box; }
  html, body {
    width: 1200px; height: 930px; overflow: hidden;
    background: var(--backdrop);
    font-family: "Bodoni Moda", "Times New Roman", serif;
  }
  .canvas { position: relative; width: 1200px; height: 930px; }
  .card {
    position: absolute; left: 318px; width: 564px; height: 323px;
    background: var(--card); overflow: hidden;
    box-shadow: 0 4px 14px rgba(0,0,0,.35);
  }
  .card--front { top: 125px; }
  .card--back { top: 514px; }

  .wordmark {
    color: var(--bronze); font-weight: 400; letter-spacing: .5px; line-height: 1;
    white-space: nowrap;
  }
  .card--front .wordmark {
    position: absolute; left: 26px; top: 58px; font-size: 44px;
  }
  .card--back .wordmark {
    position: absolute; left: 0; right: 0; top: 50%;
    transform: translateY(-50%); text-align: center; font-size: 72px;
  }

  .contact { position: absolute; left: 26px; top: 143px; color: var(--ink); }
  .contact__name {
    color: var(--bronze); font-weight: 600; font-size: 25px; line-height: 1;
    white-space: nowrap;
  }
  .contact__role { font-size: 14px; margin-top: 5px; }
  .contact__address { font-size: 14px; line-height: 19px; margin-top: 9px; letter-spacing: .2px; }
  .contact__list { list-style: none; margin-top: 8px; font-size: 14px; line-height: 19px; letter-spacing: .2px; }
  .contact__list li { display: flex; align-items: center; gap: 8px; white-space: nowrap; }
  .contact__list svg { width: 9px; height: 9px; flex: none; }

  .portrait {
    position: absolute; left: 278px; top: 0; width: 286px; height: 323px;
    background: linear-gradient(100deg, var(--photo-light) 0%, var(--photo-mid) 55%, var(--photo-shade) 100%);
  }
</style>
</head>
<body>
<main class="canvas">
  <section class="card card--front">
    <div class="wordmark">Lashvera</div>
    <div class="contact">
      <div class="contact__name">Clara M. Wendell</div>
      <div class="contact__role">Director</div>
      <div class="contact__address">4720 N.Alder Crest Ave<br>Beverly Hills , CA 90210</div>
      <ul class="contact__list">
        <li>
          <svg viewBox="0 0 10 10" aria-hidden="true"><path d="M2 1 L4 1 L4.6 3 L3.5 4 Q4.5 6 6 6.5 L7 5.4 L9 6 L9 8 Q8 9 6.5 8.7 Q2 7.5 1.2 3 Q1 1.8 2 1Z" fill="var(--bronze)"/></svg>
          310.555.0148
        </li>
        <li>
          <svg viewBox="0 0 10 10" aria-hidden="true"><rect x="1" y="2.5" width="8" height="5.5" fill="none" stroke="var(--bronze)" stroke-width="1"/><path d="M1 2.5 L5 5.5 L9 2.5" fill="none" stroke="var(--bronze)" stroke-width="1"/></svg>
          hello@lashverastudio.example
        </li>
        <li>
          <svg viewBox="0 0 10 10" aria-hidden="true"><circle cx="5" cy="5" r="4" fill="none" stroke="var(--bronze)" stroke-width="1"/><ellipse cx="5" cy="5" rx="1.8" ry="4" fill="none" stroke="var(--bronze)" stroke-width=".8"/><path d="M1 5 H9" stroke="var(--bronze)" stroke-width=".8"/></svg>
          www.lashverastudio.example
        </li>
      </ul>
    </div>
    <div class="portrait" role="img" aria-label="Black and white beauty photograph showcasing lash extensions"></div>
  </section>

  <section class="card card--back">
    <div class="wordmark">Lashvera</div>
  </section>
</main>
</body>
</html>
```